Dovecote Realty

Business cards for 4 people

They need to say for all
87 Tarrow Quay, Boston MA 02114

Each person will have their own personal information
We would like gold embossing for the name of the company
Marla is the blonde sitting in the chair smiling her information should be on the back of the card with her name and information
Should say for slogan classic pattern, elevated experience
grace@dovecoteprops.com
(413) 555-0182

Odette is the brunette with wavy hair in the tan suit odette@dovecoteprops.com
(617) 555-0137

faith@dovecoteprops.com
(413) 555-0164
standing next to the chair

hope@dovecoteprops.com
(413) 555-0199
close up headshot

```html
<!DOCTYPE html>
<html lang="en">
<head>
<meta charset="utf-8">
<title>Dovecote Realty — Business Cards</title>
<link rel="stylesheet" href="https://fonts.googleapis.com/css2?family=Open+Sans:wght@400;700&display=swap">
<style>
  :root {
    --backdrop: #222222;
    --navy: #1f2d4e;
    --emboss: #2c4078;
    --gold: #e2b264;
    --white: #ffffff;
    --photo-light: #fbf8f0;
    --photo-warm: #8a5e3c;
  }
  * { box-sizing: border-box; margin: 0; padding: 0; }
  html, body {
    width: 1200px; height: 780px; overflow: hidden;
    background: var(--backdrop);
    font-family: "Open Sans", Arial, sans-serif;
  }
  .canvas {
    width: 1200px; height: 780px;
    display: flex; align-items: center; justify-content: center; gap: 40px;
  }
  .card {
    position: relative;
    width: 540px; height: 309px;
    background: var(--navy);
    border-radius: 3px;
    overflow: hidden;
    box-shadow: 0 14px 30px rgba(0,0,0,.45);
  }

  /* Front */
  .brand {
    position: absolute; left: 176px; top: 20px;
    display: flex; align-items: center; gap: 10px;
    color: var(--gold);
    font-weight: 400; font-size: 14px; letter-spacing: 1.5px;
    text-transform: uppercase;
  }
  .brand-dot {
    width: 38px; height: 38px; border-radius: 50%;
    border: 2px solid var(--gold);
  }
  .name-band {
    position: absolute; left: 0; top: 76px;
    width: 330px; height: 56px;
    background: linear-gradient(90deg, var(--gold) 0%, #b59068 20%, #6b6275 55%, rgba(31,45,78,0) 100%);
  }
  .person-name {
    position: absolute; left: 30px; top: 78px;
    color: var(--white); font-weight: 700; font-size: 25px; line-height: 1.1;
    white-space: nowrap;
  }
  .person-title {
    position: absolute; left: 30px; top: 111px;
    color: var(--white); font-size: 10px; white-space: nowrap;
  }
  .contact {
    position: absolute; left: 30px; top: 146px;
    color: var(--gold); font-size: 12.5px; line-height: 1.5;
    list-style: none; white-space: nowrap;
  }
  .contact li { display: flex; align-items: center; gap: 7px; }
  .contact .address { padding-left: 19px; }
  .contact svg { width: 12px; height: 12px; flex: none; }
  .portrait {
    position: absolute; left: 334px; top: 108px;
    width: 180px; height: 180px; border-radius: 50%;
    border: 4px solid var(--gold);
    background: radial-gradient(circle at 45% 55%, var(--photo-warm) 0%, #a77a52 38%, var(--photo-light) 72%);
  }

  /* Back */
  .card-back { display: flex; align-items: center; justify-content: center; }
  .emboss-mark {
    display: flex; align-items: center; gap: 16px;
    color: var(--emboss);
    font-weight: 400; font-size: 30px; letter-spacing: 3px;
    text-transform: uppercase;
  }
  .emboss-dot {
    width: 86px; height: 86px; border-radius: 50%;
    border: 3px solid var(--emboss);
  }
</style>
</head>
<body>
<main class="canvas">
  <section class="card card-front" aria-label="Business card front">
    <div class="brand"><span class="brand-dot"></span><span>Dovecote Realty</span></div>
    <div class="name-band"></div>
    <h1 class="person-name">Odette Varnell</h1>
    <p class="person-title">Real Estate Advisor and Sales Manager</p>
    <ul class="contact">
      <li class="address">87 Tarrow Quay,</li>
      <li class="address">Boston MA 02114</li>
      <li>
        <svg viewBox="0 0 24 24" fill="currentColor" aria-hidden="true"><path d="M6.6 10.8a15.1 15.1 0 0 0 6.6 6.6l2.2-2.2a1 1 0 0 1 1-.25 11.4 11.4 0 0 0 3.6.57 1 1 0 0 1 1 1V20a1 1 0 0 1-1 1A17 17 0 0 1 3 4a1 1 0 0 1 1-1h3.5a1 1 0 0 1 1 1c0 1.25.2 2.45.57 3.57a1 1 0 0 1-.25 1z"/></svg>
        (617) 555-0137
      </li>
      <li>
        <svg viewBox="0 0 24 24" fill="none" stroke="currentColor" stroke-width="2" aria-hidden="true"><circle cx="12" cy="12" r="9"/><path d="M3 12h18M12 3c3 3 3 15 0 18M12 3c-3 3-3 15 0 18"/></svg>
        www.dovecoteprops.com
      </li>
      <li>
        <svg viewBox="0 0 24 24" fill="none" stroke="currentColor" stroke-width="2" aria-hidden="true"><rect x="3" y="5" width="18" height="14" rx="1"/><path d="M3 6l9 7 9-7"/></svg>
        odette@dovecoteprops.com
      </li>
    </ul>
    <div class="portrait" role="img" aria-label="Portrait photo of Odette, brunette with wavy hair in a tan suit"></div>
  </section>

  <section class="card card-back" aria-label="Business card back">
    <div class="emboss-mark"><span>Dovecote Realty</span><span class="emboss-dot"></span></div>
  </section>
</main>
</body>
</html>
```